Wedding Videography Wordpress Website Theme

We need a modern and high-end website look for our wedding video and film business. We film weddings all over the United Kingdom and at European destinations so need something to reflect our work. The website should be visually stunning with images and videos being the focal point as this is what our services are.

The current website is www.brunolessway.com so you will be able to see our brand.

My Instagram is www.instagram.com/brunolesswayfilms so a new design should link in with this idea.

We need the following pages designed by the winning designer

1 - Homepage
2 - Films Index Page
3 - Testimonials
4 - Prices
5 - Reviews
6 - Meet Bruno (About)
7 - Contact
8 - Blog Index
9 - Blog Page

All pages must be consistent so have a similar style.

Pages on menu:
Meet Bruno
Videos
Packages
Testimionials
Journal (Blog)
Contact

We require a responsive look too. Over 90% of our visitors access the website via their mobile devices.

```html
<!DOCTYPE html>
<html lang="en">
<head>
<meta charset="utf-8">
<title>Enquire – Bruno Lessway Wedding Films</title>
<link rel="stylesheet" href="https://fonts.googleapis.com/css2?family=Cormorant+Garamond:wght@500;600&family=Jost:wght@300;400;500;600&display=swap">
<style>
:root{
  --gold:#a58a4c;
  --gold-dark:#8d733a;
  --cream:#f7edd4;
  --button:#e6d5a8;
  --sand:#e9dbb7;
  --linen:#f3ebdd;
  --panel:#f6f5f3;
  --ink:#2b2b2b;
  --muted:#8a8a8a;
  --line:#e4e4e4;
  --white:#ffffff;
}
*{box-sizing:border-box;margin:0;padding:0}
html,body{width:1200px;height:3308px;overflow:hidden}
body{position:relative;font-family:'Jost',sans-serif;color:var(--ink);background:var(--white)}
.abs{position:absolute}
.serif{font-family:'Cormorant Garamond',serif}

/* hero */
.hero{left:0;top:0;width:1200px;height:616px;background:linear-gradient(180deg,#6f6d5c 0%,#a39a78 30%,#8e7c5e 60%,#4b4337 100%)}
.brand{left:112px;top:70px;width:200px;text-align:center;color:var(--white)}
.brand-name{font-size:19px;letter-spacing:4px;font-weight:400}
.brand-sub{font-size:8px;letter-spacing:5px;margin-top:4px}
.brand-mark{display:block;width:22px;height:22px;border:1.5px solid currentColor;margin:0 auto 14px}
.nav{top:80px;left:396px;display:flex;gap:42px;color:var(--white);font-size:12px;font-weight:500;letter-spacing:.3px}
.nav-cta{left:940px;top:63px;width:145px;height:46px;background:var(--button);color:var(--ink);font-size:12px;font-weight:500;display:flex;align-items:center;justify-content:center}
.hero-title{left:0;width:1200px;top:296px;text-align:center;color:#f1e6c8;font-size:40px;letter-spacing:2px;font-weight:500}
.hero-sub{left:0;width:1200px;top:352px;text-align:center;color:var(--white);font-size:16px;font-weight:500;letter-spacing:.5px}

/* chat */
.section-title{left:0;width:1200px;text-align:center;color:var(--gold);font-size:30px;font-weight:600;letter-spacing:1px}
.contact-card{top:757px;height:107px;background:var(--cream);display:flex;align-items:center;padding-left:48px;gap:28px}
.contact-card small{display:block;font-size:12px;color:#555;margin-bottom:6px}
.contact-card strong{font-size:20px;font-weight:400;letter-spacing:.3px}
.chat-note{left:160px;width:880px;top:898px;text-align:center;font-size:13px;line-height:26px;color:#444;font-weight:300}
.chat-note b{font-weight:600;color:var(--ink)}

/* form */
.venue-photo{left:114px;top:1010px;width:475px;height:645px;background:linear-gradient(180deg,#c6ccc9 0%,#7e8c6a 28%,#8c7a5c 55%,#5f8a3a 78%,#4e7e2e 100%)}
.form-panel{left:589px;top:1010px;width:493px;height:645px;background:var(--panel)}
.form-title{left:638px;top:1042px;color:var(--gold);font-size:31px;font-weight:600;letter-spacing:.5px}
.field{background:var(--white);border:1px solid var(--line);font-size:12px;color:var(--muted);font-weight:300;padding:0 20px;display:flex;align-items:center;justify-content:space-between}
.field.area{align-items:flex-start;padding-top:16px}
.submit{left:637px;top:1563px;width:196px;height:46px;background:var(--button);font-size:14px;font-weight:500;display:flex;align-items:center;justify-content:center}

/* testimonials */
.testimonials{left:0;top:1745px;width:1200px;height:758px;background:linear-gradient(180deg,var(--linen),#efe5d2)}
.film{background:linear-gradient(160deg,#2c3326 0%,#6e6d64 45%,#8e8a80 100%)}
.film-side-l{left:0;top:1913px;width:237px;height:330px;background:linear-gradient(160deg,#4b5a3a,#9fa593)}
.film-side-r{left:962px;top:1913px;width:238px;height:330px;background:linear-gradient(160deg,#3e3a36,#cfc8bd)}
.play{left:573px;top:2052px;width:52px;height:52px;border-radius:50%;background:rgba(255,255,255,.35);display:flex;align-items:center;justify-content:center}
.play span{width:34px;height:34px;border-radius:50%;background:var(--white);display:flex;align-items:center;justify-content:center}
.film-caption{left:280px;width:638px;top:2118px;text-align:center;color:var(--white);font-family:'Cormorant Garamond',serif;font-style:italic;font-size:34px;font-weight:600}
.arrow{top:2224px;width:53px;height:39px;display:flex;align-items:center;justify-content:center}
.quote{left:330px;width:560px;top:2294px;text-align:center;font-size:14px;line-height:27px;color:#333;font-weight:300}
.attrib{left:0;width:1200px;top:2400px;display:flex;align-items:center;justify-content:center;gap:14px;color:var(--gold);font-size:14px;font-weight:500}
.attrib i{display:block;width:24px;height:1px;background:var(--gold)}

/* instagram */
.insta{left:0;top:2503px;width:1200px;height:469px;background:var(--sand)}
.insta-title{left:0;width:1200px;top:2562px;text-align:center;color:#8f7f5f;font-size:29px;letter-spacing:8px;font-weight:500}
.tile{top:2648px;width:144px;height:162px}
.follow{left:471px;top:2860px;width:257px;height:56px;background:var(--white);font-size:14px;display:flex;align-items:center;justify-content:center}

/* footer */
.foot-brand{left:108px;top:3075px;width:200px;text-align:center;color:#d2bd86}
.social{top:3155px;width:26px;height:24px;border:1.5px solid #d2bd86;border-radius:4px}
.foot-head{font-size:17px;font-weight:400;display:flex;align-items:center;gap:10px;color:#333}
.foot-head i{display:block;width:24px;height:1px;background:#aaa}
.foot-item{font-size:13px;color:#333;font-weight:300;display:flex;align-items:center;gap:18px}
.foot-link{font-size:13px;color:#333;font-weight:300}
.copyright{left:0;width:1200px;top:3229px;text-align:center;font-size:11px;color:#777;font-weight:300}
</style>
</head>
<body>

<header class="abs hero" role="img" aria-label="Photo of a laughing bride and friends celebrating on a sunny terrace"></header>
<div class="abs brand">
  <span class="brand-mark"></span>
  <div class="brand-name">BRUNO LESSWAY</div>
  <div class="brand-sub">WEDDING FILMS</div>
</div>
<nav class="abs nav"><span>MEET BRUNO</span><span>VIDEOS</span><span>PACKAGES</span><span>TESTIMONIALS</span><span>JOURNAL</span></nav>
<div class="abs nav-cta">ENQUIRE</div>
<h1 class="abs hero-title serif">ENQUIRE</h1>
<p class="abs hero-sub">Contact me today</p>

<h2 class="abs section-title serif" style="top:678px">READY FOR A CHAT?</h2>
<div class="abs contact-card" style="left:240px;width:348px">
  <svg width="52" height="52" viewBox="0 0 52 52" fill="none" stroke="#a58a4c" stroke-width="2"><path d="M12 6l8 10-4 5c2 6 8 12 14 14l5-4 10 8-5 7C26 46 6 26 5 11z"/><path d="M30 8a14 14 0 0 1 14 14M30 14a8 8 0 0 1 8 8"/></svg>
  <div><small>Call Me:</small><strong>07700 900123</strong></div>
</div>
<div class="abs contact-card" style="left:608px;width:343px;padding-left:32px">
  <svg width="56" height="52" viewBox="0 0 56 52" fill="none" stroke="#a58a4c" stroke-width="2"><path d="M4 22v26h46V22"/><path d="M4 22l23 16 23-16"/><path d="M4 48l17-13M50 48L33 35"/><path d="M12 26V8h24l6 6v12"/><circle cx="44" cy="12" r="6"/><path d="M17 15h14M17 21h14"/></svg>
  <div><small>Email Me:</small><strong>films@brunolessway.com</strong></div>
</div>
<p class="abs chat-note">I'll respond in a couple of hours or so. Before enquiring please check my prices to see if I am within your budget. <b>Click here for my packages.</b> We can chat about your wedding plans, check my availability, and see if we're a match made in heaven.</p>

<section>
  <div class="abs venue-photo" role="img" aria-label="Aerial photo of a stately stone hall with wedding guests on the lawn"></div>
  <div class="abs form-panel"></div>
  <h2 class="abs form-title serif">GET IN TOUCH</h2>
  <div class="abs field" style="left:636px;top:1105px;width:411px;height:47px">How did you hear about my wedding films?<svg width="14" height="8" viewBox="0 0 14 8" fill="none" stroke="#999"><path d="M1 1l6 6 6-6"/></svg></div>
  <div class="abs field" style="left:636px;top:1172px;width:198px;height:48px">First name</div>
  <div class="abs field" style="left:848px;top:1172px;width:199px;height:48px">Last name</div>
  <div class="abs field" style="left:636px;top:1239px;width:198px;height:48px">Email address</div>
  <div class="abs field" style="left:848px;top:1239px;width:199px;height:48px">Mobile number</div>
  <div class="abs field" style="left:636px;top:1306px;width:411px;height:48px">When is your wedding day?<svg width="22" height="22" viewBox="0 0 22 22" fill="none" stroke="#999"><rect x="1" y="3" width="20" height="18" rx="2"/><path d="M1 8h20M6 1v4M16 1v4M5 12h2M10 12h2M15 12h2M5 16h2M10 16h2"/></svg></div>
  <div class="abs field" style="left:636px;top:1374px;width:411px;height:48px">What time is your wedding ceremony?<svg width="22" height="22" viewBox="0 0 22 22" fill="none" stroke="#999"><circle cx="11" cy="11" r="10"/><path d="M11 5v6l4 3"/></svg></div>
  <div class="abs field area" style="left:636px;top:1441px;width:411px;height:99px">what are you planning for your wedding day?</div>
  <div class="abs submit">Submit</div>
</section>

<section>
  <div class="abs testimonials"></div>
  <h2 class="abs section-title serif" style="top:1818px">WEDDING VIDEO TESTIMONIALS</h2>
  <div class="abs film-side-l" role="img" aria-label="Wedding film still of a couple embracing outdoors"></div>
  <div class="abs film-side-r" role="img" aria-label="Wedding film still of newlyweds leaving under confetti"></div>
  <div class="abs film" style="left:280px;top:1891px;width:638px;height:372px" role="img" aria-label="Wedding film still of a bride and groom walking along a path"></div>
  <div class="abs play"><span><svg width="12" height="14" viewBox="0 0 12 14"><path d="M1 1l10 6-10 6z" fill="#555"/></svg></span></div>
  <div class="abs film-caption">Imara &amp; Leo</div>
  <div class="abs arrow" style="left:280px;background:var(--white)"><svg width="22" height="12" viewBox="0 0 22 12" fill="none" stroke="#888" stroke-width="1.5"><path d="M21 6H2M7 1L2 6l5 5"/></svg></div>
  <div class="abs arrow" style="left:865px;background:var(--button)"><svg width="22" height="12" viewBox="0 0 22 12" fill="none" stroke="#222" stroke-width="1.5"><path d="M1 6h19M15 1l5 5-5 5"/></svg></div>
  <p class="abs quote">We have a really emotional video for our wedding. It is a beauty video that is going to stay with us for the rest of our lives. Bruno was everywhere but you couldn't tell he was there. He was a really fun guy and we now consider him a friend.”</p>
  <div class="abs attrib"><i></i>Married at Villa Serena, Umbria, Italy<i></i></div>
</section>

<section>
  <div class="abs insta"></div>
  <h2 class="abs insta-title serif">FOLLOW ME ON INSTAGRAM</h2>
  <div class="abs tile" style="left:114px;background:linear-gradient(160deg,#c9c2b6,#6f675c)" role="img" aria-label="Couple walking down a village street"></div>
  <div class="abs tile" style="left:279px;background:linear-gradient(160deg,#8c8f86,#3f4752)" role="img" aria-label="Groom and laughing bride under confetti"></div>
  <div class="abs tile" style="left:445px;background:linear-gradient(180deg,#c8cdd0,#9c9a78)" role="img" aria-label="White horse-drawn carriage in a field"></div>
  <div class="abs tile" style="left:609px;background:linear-gradient(160deg,#8d9a7c,#2e2e2e)" role="img" aria-label="Father walking the bride down the aisle"></div>
  <div class="abs tile" style="left:775px;background:linear-gradient(160deg,#4f5a45,#cfc5b8)" role="img" aria-label="Bride smiling at groom during ceremony"></div>
  <div class="abs tile" style="left:940px;background:linear-gradient(180deg,#5d7fb0,#7a8a5a)" role="img" aria-label="Wedding party jumping against a blue sky"></div>
  <div class="abs follow">Follow me @brunolesswayfilms</div>
</section>

<footer>
  <div class="abs foot-brand">
    <span class="brand-mark"></span>
    <div class="brand-name">BRUNO LESSWAY</div>
    <div class="brand-sub">WEDDING FILMS</div>
  </div>
  <div class="abs social" style="left:153px"></div>
  <div class="abs social" style="left:198px"></div>
  <div class="abs social" style="left:243px;width:30px"></div>

  <div class="abs foot-head" style="left:412px;top:3050px">Contact <i></i></div>
  <div class="abs foot-item" style="left:412px;top:3097px"><svg width="18" height="18" viewBox="0 0 18 18" fill="none" stroke="#999"><path d="M4 1l3 4-2 2c1 3 3 5 6 6l2-2 4 3-2 3C7 17 1 11 1 3z"/></svg>07700 900123</div>
  <div class="abs foot-item" style="left:412px;top:3145px"><svg width="18" height="14" viewBox="0 0 18 14" fill="none" stroke="#999"><rect x="1" y="1" width="16" height="12"/><path d="M1 1l8 6 8-6"/></svg>films@brunolessway.com</div>

  <div class="abs foot-head" style="left:699px;top:3051px">Links <i></i></div>
  <div class="abs foot-link" style="left:703px;top:3091px">FAQ's</div>
  <div class="abs foot-link" style="left:703px;top:3125px">Wedding Photography</div>
  <div class="abs foot-link" style="left:703px;top:3159px">Commercial</div>
  <div class="abs foot-link" style="left:918px;top:3091px">North East Wedding Venues</div>
  <div class="abs foot-link" style="left:918px;top:3125px">Free Speeches Guide</div>
  <div class="abs foot-link" style="left:918px;top:3159px">Blog</div>

  <p class="abs copyright">© Copyright 2022 Bruno Lessway Films Ltd All Rights Reserved</p>
</footer>

</body>
</html>
```